Packaging design for a reclosable bag for our product

We have a logo, and we need to put it on packaging for our product and while we want the look to be simple, we want it to follow good design principles and also contain spaces for other product descriptions.

There will be 5 sizes at launch so I'd like 5 variations, one for each size.

I've included a few mockups of the type of bag that I made but they are all just rough ideas that I had.

I want the brand to look scientific and methodical and even a bit quirky, as in "wow this is a serious product but also a bit unusual."

```html
<!DOCTYPE html>
<html lang="en">
<head>
<meta charset="utf-8">
<title>KV3 Pouch Packaging – Black and White Colourways</title>
<link rel="stylesheet" href="https://fonts.googleapis.com/css2?family=Open+Sans:wght@300;700&display=swap">
<style>
  :root {
    --page-bg: #ffffff;
    --pouch-black: #0d0d0d;
    --pouch-white: #f1f1f1;
    --pouch-white-edge: #e2e2e2;
    --band-grey: #8c8c8c;
    --band-grey-light: #8a8a8a;
    --mark-on-black: #0d0d0d;
    --mark-on-white: #f1f1f1;
    --spec-on-black: #3b3b3b;
    --spec-on-white: #8e8e8e;
  }
  * { box-sizing: border-box; margin: 0; padding: 0; }
  html, body {
    width: 1200px;
    height: 1040px;
    overflow: hidden;
    background: var(--page-bg);
    font-family: "Open Sans", sans-serif;
  }
  .canvas {
    position: relative;
    width: 1200px;
    height: 1040px;
  }
  .pouch {
    position: absolute;
    top: 76px;
    width: 448px;
    height: 648px;
    border-radius: 14px 14px 0 0;
  }
  .pouch--black {
    left: 152px;
    background: var(--pouch-black);
  }
  .pouch--white {
    left: 652px;
    height: 652px;
    width: 436px;
    background: var(--pouch-white);
    border: 1px solid var(--pouch-white-edge);
  }
  .brand-band {
    position: absolute;
    left: 5px;
    top: 474px;
    width: 206px;
    height: 95px;
    display: flex;
    align-items: center;
    justify-content: center;
  }
  .pouch--black .brand-band { background: var(--band-grey); }
  .pouch--white .brand-band { background: var(--band-grey-light); }
  .brand-name {
    font-weight: 700;
    font-size: 74px;
    letter-spacing: -2px;
    line-height: 1;
  }
  .pouch--black .brand-name { color: var(--mark-on-black); }
  .pouch--white .brand-name { color: var(--mark-on-white); }
  .spec-list {
    position: absolute;
    left: 226px;
    top: 473px;
    list-style: none;
    font-weight: 300;
    font-size: 15.5px;
    line-height: 20px;
    white-space: nowrap;
  }
  .pouch--white .spec-list { left: 224px; top: 476px; }
  .pouch--black .spec-list { color: var(--spec-on-black); }
  .pouch--white .spec-list { color: var(--spec-on-white); }
</style>
</head>
<body>
<main class="canvas">
  <section class="pouch pouch--black" aria-label="Black pouch colourway">
    <div class="brand-band"><span class="brand-name">KV3</span></div>
    <ul class="spec-list">
      <li>5 Meters</li>
      <li>Extra Large</li>
      <li>Bias Lighting</li>
      <li>Simulated D65 CRI 90+</li>
      <li>6500K White</li>
    </ul>
  </section>
  <section class="pouch pouch--white" aria-label="White pouch colourway">
    <div class="brand-band"><span class="brand-name">KV3</span></div>
    <ul class="spec-list">
      <li>5 Meters</li>
      <li>Extra Large</li>
      <li>Bias Lighting</li>
      <li>Simulated D65 CRI 90+</li>
      <li>6500K White</li>
    </ul>
  </section>
</main>
</body>
</html>
```